Vantor Ridge needs a Business Card Design

We need a business card design for an Information Technology company based in Fairfax Virginia called Vantor Ridge. We want the business card to use our logo colors. We need it to be double-sided. The business card needs to look professional but we would like it to be unique. You can get company information from our web site (http://www.vantorridgellc.example).

Target Market(s)

Target market is Government Agencies and Business Professionals.

Industry/Entity Type

Business

Requirements
Must have
• Must have section for company name, company address, company URL, employee name, title, phone and email. Also must have company logo and space for entering logos.

```html
<!DOCTYPE html>
<html lang="en">
<head>
<meta charset="utf-8">
<title>Vantor Ridge Business Card</title>
<link href="https://fonts.googleapis.com/css2?family=Open+Sans:wght@400;600;700;800&display=swap" rel="stylesheet">
<style>
  :root {
    --backdrop: #e9e6e1;
    --card: #ffffff;
    --navy: #23339a;
    --royal: #2a48a8;
    --sky: #1f7cc4;
    --ink: #4a4a4a;
    --rule: #3a4aa0;
  }
  * { margin: 0; padding: 0; box-sizing: border-box; }
  html, body { width: 1200px; height: 1024px; overflow: hidden; }
  body {
    background: var(--backdrop);
    font-family: "Open Sans", Arial, sans-serif;
    position: relative;
  }
  .card {
    position: absolute;
    left: 250px;
    width: 700px;
    height: 400px;
    background: var(--card);
    box-shadow: 0 6px 18px rgba(0,0,0,0.18);
    overflow: hidden;
  }
  .card--front { top: 70px; }
  .card--back { top: 554px; }

  .brand-name {
    font-weight: 800;
    color: var(--navy);
    text-transform: uppercase;
    letter-spacing: 0.5px;
    line-height: 1;
    display: flex;
    align-items: center;
    gap: 14px;
  }
  .brand-mark {
    width: 34px; height: 34px;
    background: var(--navy);
    flex: none;
  }
  .tagline {
    font-size: 11px;
    font-weight: 600;
    text-transform: uppercase;
    color: var(--ink);
    letter-spacing: 0.3px;
  }

  /* front */
  .front-brand { position: absolute; left: 56px; top: 70px; }
  .front-brand .brand-name { font-size: 38px; }
  .front-brand .tagline { margin: 6px 0 0 48px; }

  .person { position: absolute; left: 56px; top: 228px; }
  .person__name { font-size: 17px; font-weight: 700; color: var(--navy); }
  .person__title { font-size: 14px; color: var(--sky); margin-top: 2px; }
  .person__address { display: flex; gap: 8px; margin-top: 8px; font-size: 14px; color: var(--ink); line-height: 1.4; }
  .person__address svg { flex: none; margin-top: 3px; }

  .divider {
    position: absolute; left: 392px; top: 180px;
    width: 1.5px; height: 90px;
    background: linear-gradient(to bottom, rgba(58,74,160,0), var(--rule), rgba(58,74,160,0));
  }

  .contacts { position: absolute; left: 430px; top: 175px; list-style: none; }
  .contacts li { display: flex; align-items: center; gap: 8px; font-size: 14px; color: var(--ink); line-height: 22px; }
  .contacts svg { flex: none; }

  .band { position: absolute; bottom: 0; height: 34px; }
  .band--navy { left: 0; width: 560px; background: var(--navy); }
  .band--sky { left: 574px; width: 126px; height: 46px; background: var(--sky); }

  /* back */
  .back-brand { position: absolute; left: 0; right: 0; top: 120px; display: flex; flex-direction: column; align-items: center; }
  .back-brand .brand-name { font-size: 46px; }
  .back-brand .tagline { font-size: 13px; margin-top: 8px; }
  .back-url { position: absolute; left: 56px; bottom: 56px; font-size: 14px; color: var(--royal); }
</style>
</head>
<body>

<section class="card card--front" aria-label="Business card front">
  <div class="front-brand">
    <div class="brand-name"><span class="brand-mark"></span>Vantor Ridge</div>
    <div class="tagline">Turning Bold Ideas Into Real Results</div>
  </div>

  <div class="person">
    <div class="person__name">Daniel Okafor</div>
    <div class="person__title">Job Title</div>
    <div class="person__address">
      <svg width="13" height="13" viewBox="0 0 12 12" aria-hidden="true"><path d="M6 1 L11 6 H9.5 V11 H7 V8 H5 V11 H2.5 V6 H1 Z" fill="#23339a"/></svg>
      <span>4180 Meridian Ct, Suite 300<br>Fairfax, VA 22030</span>
    </div>
  </div>

  <div class="divider"></div>

  <ul class="contacts">
    <li><svg width="12" height="12" viewBox="0 0 12 12" aria-hidden="true"><path d="M3 1 L5 3.5 L4 5 C4.8 6.6 5.6 7.4 7 8 L8.5 7 L11 9 L9.6 11 C5.5 10.6 1.4 6.5 1 2.4 Z" fill="#1f7cc4"/></svg>800.555.0142</li>
    <li><svg width="12" height="12" viewBox="0 0 12 12" aria-hidden="true"><rect x="2" y="4" width="8" height="6" rx="1" fill="#1f7cc4"/><rect x="3.5" y="1" width="5" height="3" fill="#1f7cc4"/></svg>800.555.0187</li>
    <li><svg width="12" height="12" viewBox="0 0 12 12" aria-hidden="true"><rect x="1" y="2.5" width="10" height="7" rx="1" fill="#1f7cc4"/><path d="M1.5 3 L6 6.5 L10.5 3" stroke="#fff" stroke-width="1" fill="none"/></svg>name@vantorridgellc.example</li>
    <li><svg width="12" height="12" viewBox="0 0 12 12" aria-hidden="true"><circle cx="6" cy="6" r="5" fill="#1f7cc4"/><path d="M1 6 H11 M6 1 C3.5 4 3.5 8 6 11 M6 1 C8.5 4 8.5 8 6 11" stroke="#fff" stroke-width="0.8" fill="none"/></svg>www.vantorridgellc.example</li>
  </ul>

  <div class="band band--navy"></div>
  <div class="band band--sky"></div>
</section>

<section class="card card--back" aria-label="Business card back">
  <div class="back-brand">
    <div class="brand-name"><span class="brand-mark"></span>Vantor Ridge</div>
    <div class="tagline">Turning Bold Ideas Into Real Results</div>
  </div>
  <div class="back-url">www.vantorridgellc.example</div>
</section>

</body>
</html>
```